Corporate Design für Brackway Living
Zielgruppe
Kauf, Vermietung, Bewirtschaftung und Optimierung von Wohnimmobilien. Zielgruppe sind Immobilienmakler, Banken und private Hausverkäufer.
Aufgabenstellung
Als Vorgabe möchte ich das nicht bestimmen, jedoch würde ich als Farbwahl blau-weiß oder etwas in die maritime Richtung bevorzugen.

```html
<!DOCTYPE html>
<html lang="de">
<head>
<meta charset="utf-8">
<title>Brackway Living – Geschäftsausstattung</title>
<link href="https://fonts.googleapis.com/css2?family=Mulish:wght@400;500&display=swap" rel="stylesheet">
<style>
  :root {
    --brand-blue: #00508f;
    --paper: #ffffff;
    --ink: #4a4a4a;
    --ink-dark: #2b2b2b;
    --window-grey: #bdbdbd;
    --flap-line: #dedede;
    --backdrop: #e9e6e1;
    --shadow: 0 2px 6px rgba(0,0,0,.25);
  }
  * { box-sizing: border-box; margin: 0; padding: 0; }
  html, body { width: 764px; height: 1200px; overflow: hidden; }
  body {
    position: relative;
    background: var(--backdrop);
    font-family: "Mulish", sans-serif;
    color: var(--ink);
  }
  .sheet { position: absolute; background: var(--paper); box-shadow: var(--shadow); }
  .wordmark {
    position: absolute;
    color: var(--brand-blue);
    font-weight: 400;
    white-space: nowrap;
    letter-spacing: .2px;
  }
  .brand-square { position: absolute; background: var(--brand-blue); }
  .brand-square--light { background: var(--paper); }

  /* Folder */
  .folder { left: 348px; top: 139px; width: 384px; height: 543px; background: var(--brand-blue); }
  .folder .brand-square { left: 170px; top: 255px; width: 44px; height: 44px; }

  /* Letterhead */
  .letterhead { left: 35px; top: 39px; width: 380px; height: 537px; }
  .letterhead .wordmark { left: 0; right: 0; top: 27px; text-align: center; font-size: 20px; }
  .fold-mark { position: absolute; left: 2px; width: 6px; height: 1px; background: #bbb; }
  .letter-footer .col {
    position: absolute; top: 505px;
    font-size: 4.6px; line-height: 7px; color: var(--ink);
    white-space: nowrap;
  }
  .letter-footer .col--company { left: 18px; }
  .letter-footer .col--contact { left: 86px; }
  .letter-footer .col--register { left: 160px; }
  .letter-footer .col--bank { left: 260px; }
  .letterhead .brand-square { left: 343px; top: 496px; width: 20px; height: 20px; }

  /* Business cards */
  .card-front { left: 505px; top: 653px; width: 154px; height: 100px; }
  .card-front .wordmark { left: 10px; top: 16px; font-size: 15px; }
  .card-front .person { position: absolute; left: 48px; top: 54px; white-space: nowrap; }
  .card-front .name { font-size: 7px; font-weight: 500; color: var(--ink-dark); }
  .card-front .role { font-size: 4.2px; margin-top: 2px; }
  .card-front .contact { font-size: 4.2px; line-height: 6px; margin-top: 6px; }

  .card-back { left: 506px; top: 768px; width: 154px; height: 100px; background: var(--brand-blue); }
  .card-back .url { position: absolute; left: 58px; top: 48px; font-size: 6px; color: var(--paper); white-space: nowrap; }
  .card-back .brand-square { left: 124px; top: 38px; width: 22px; height: 22px; }

  /* Envelope front */
  .envelope-front { left: 43px; top: 706px; width: 402px; height: 207px; }
  .envelope-front .wordmark { left: 57px; top: 46px; font-size: 19px; }
  .address-window {
    position: absolute; left: 38px; top: 98px; width: 158px; height: 80px;
    background: var(--window-grey); border-radius: 8px;
    box-shadow: inset 0 0 4px rgba(0,0,0,.25);
  }

  /* Envelope back */
  .envelope-back { left: 254px; top: 939px; width: 403px; height: 207px; }
  .envelope-back svg { position: absolute; left: 0; top: 0; }
  .envelope-back .brand-square { left: 184px; top: 60px; width: 34px; height: 34px; }
  .envelope-back .url {
    position: absolute; left: 0; right: 0; top: 163px;
    text-align: center; font-size: 6.5px; color: var(--brand-blue);
  }
</style>
</head>
<body>

  <section class="sheet folder" aria-label="Präsentationsmappe">
    <div class="brand-square brand-square--light"></div>
  </section>

  <section class="sheet letterhead" aria-label="Briefbogen">
    <div class="wordmark">Brackway Living</div>
    <span class="fold-mark" style="top:190px"></span>
    <span class="fold-mark" style="top:380px"></span>
    <div class="letter-footer">
      <div class="col col--company">Brackway Living GmbH<br>Lindenweg 8<br>24103 Kiel</div>
      <div class="col col--contact">T: +49 (0) 431 98 765<br>E: info@brackwayliving.de<br>W: www.brackwayliving.de</div>
      <div class="col col--register">Registergericht:<br>Amtsgericht Kiel HRB 48215<br>UID: DE 274 913 560</div>
      <div class="col col--bank">Bankinstitut<br>IBAN: DE 00123456780012345678<br>BIC: ABCDDE00XXX</div>
    </div>
    <div class="brand-square"></div>
  </section>

  <section class="sheet card-front" aria-label="Visitenkarte Vorderseite">
    <div class="wordmark">Brackway Living</div>
    <div class="person">
      <div class="name">Jonas Feldberg</div>
      <div class="role">Geschäftsführer</div>
      <div class="contact">Lindenweg 8, 24103 Kiel<br>T: +49 (0) 431 98 765 | info@brackwayliving.de</div>
    </div>
  </section>

  <section class="sheet card-back" aria-label="Visitenkarte Rückseite">
    <div class="url">www.brackwayliving.de</div>
    <div class="brand-square brand-square--light"></div>
  </section>

  <section class="sheet envelope-front" aria-label="Briefumschlag Vorderseite">
    <div class="wordmark">Brackway Living</div>
    <div class="address-window"></div>
  </section>

  <section class="sheet envelope-back" aria-label="Briefumschlag Rückseite">
    <svg width="403" height="207" viewBox="0 0 403 207" aria-hidden="true">
      <path d="M3 36 L190 137 Q201 143 212 137 L397 33" fill="none" stroke="var(--flap-line)" stroke-width="2"/>
    </svg>
    <div class="brand-square"></div>
    <div class="url">www.brackwayliving.de</div>
  </section>

</body>
</html>
```